Health and Fitness Club requires a stunning and simple website

We are a health and fitness club based in Dubai, when we launch we will be the biggest club in the country, we will also have the 2 largest activity rooms in the country, we are setting a new standard in the industry by offering one thing, our attitude.

Our attitude means the following:
unlike other clubs we have no hidden charges or fees
our members can join daily, monthly, 6 months or annually
our service and facility are comparable to 5* hotel gyms
our equipment is second to none
our space is the biggest in the country
we do not force our members to use our in-house personal trainers - you can bring your own and we will not charge them entry!
we will have a cutting edge brawnmesh box in our gym with classes by the best trainers in the country
we will be providing free-lance personal trainers a platform to engage customers, grow their business and even use our activity rooms for classes

Basically we will be a gym like no other, simply because we are gym people and we hate the restrictive practices and hidden charges by other gyms, so we are making our own gym which focuses on quality and service.

All of this has to be communicated in the style of the website, the colors of the website we want to be limited to the logo colors as this will be the same theme running throughout the gym.

The landing page of the website HAS to incorporate elements from our social media presences, this basically is the usual, chirplo, snapvault, kinwall. We can have these as a sidebar, the centre of the page should display the latest article from our blog (also on the website) Also we need to have a calendar for activities and classes on the front page. The menu should have links to the following:
Latest News
About us
Team
Gallery
Membership
Classes
Member Log In
Contact Us
Location

The style of the website has to be similar to the logo, particularly in terms of the fonts used.

```html
<!DOCTYPE html>
<html lang="en">
<head>
<meta charset="utf-8">
<title>Ironhaus Health and Fitness Club</title>
<link rel="stylesheet" href="https://fonts.googleapis.com/css2?family=Open+Sans:wght@400;600;700&display=swap">
<style>
:root{
  --red:#c3161c;
  --red-dark:#9e0f14;
  --ink:#333333;
  --muted:#777777;
  --line:#e3e3e3;
  --footer:#2a2a2a;
  --cal-head:#3b3b3b;
  --white:#ffffff;
  --blue:#3b5ea8;
  --sky:#41a9e1;
  --teal:#2e8bb0;
  --rose:#d9382b;
}
*{box-sizing:border-box;margin:0;padding:0}
html,body{width:861px;height:1200px;overflow:hidden}
body{position:relative;background:var(--white);font-family:"Open Sans",Arial,sans-serif;color:var(--ink)}
.abs{position:absolute}

/* header */
.brand{left:30px;top:28px;display:flex;align-items:center;gap:10px}
.brand-dot{width:46px;height:46px;border-radius:50%;background:var(--red)}
.brand-name{font-size:22px;font-weight:700;color:var(--red)}
.search{left:615px;top:50px;width:215px;height:24px;border:1px solid #cfcfcf;border-radius:3px;display:flex;align-items:center;justify-content:space-between;padding:0 8px;font-size:10px;color:#999}

/* nav */
.main-nav{left:0;top:115px;width:861px;height:28px;background:var(--red);display:flex;justify-content:space-between;align-items:center;padding:0 50px 0 58px}
.main-nav a{color:var(--white);text-decoration:none;font-size:11.5px;font-weight:600;padding:6px 10px}
.main-nav a.is-active{background:var(--red-dark)}

/* hero */
.hero{left:0;top:143px;width:861px;height:447px;background:linear-gradient(120deg,#8f9aa0 0%,#c9c2b8 40%,#d8cbbd 60%,#7f8d96 100%)}
.hero-caption{left:260px;top:283px;width:318px;padding:14px 16px;background:rgba(55,55,55,.78);color:var(--white)}
.hero-caption h1{font-size:21px;font-weight:400;margin-bottom:6px}
.hero-caption p{font-size:10.5px;line-height:1.45;color:#eee}
.hero-arrow{top:333px;width:30px;height:30px;border-radius:50%;background:rgba(60,60,60,.7)}

/* feature boxes */
.feature{top:488px;height:215px;background:var(--red);color:var(--white);padding:14px 16px}
.feature h2{font-size:19px;font-weight:700}
.feature .sub{font-size:12px;margin:2px 0 12px}
.feature .rule{border-top:1px solid rgba(255,255,255,.35);padding-top:10px}
.class-list{list-style:none;font-size:11px}
.class-list li{display:flex;align-items:center;gap:8px;margin-bottom:11px}
.class-list .name{width:90px}
.offer{display:flex;gap:14px;align-items:center;font-size:10.5px;line-height:1.45}
.offer-icon{flex:0 0 42px;height:42px;border-radius:50%;background:var(--white);display:flex;align-items:center;justify-content:center}
.more{position:absolute;right:16px;bottom:12px;font-size:10.5px}

/* articles */
.section-title{font-size:16px;font-weight:600;color:var(--red)}
.article{left:57px;width:460px;display:flex;gap:14px}
.article-thumb{flex:0 0 95px;height:76px;background:linear-gradient(135deg,#b9b2aa,#8a8f94)}
.article h3{font-size:12px;font-weight:400;color:var(--red);margin-bottom:4px}
.article p{font-size:9px;line-height:1.4;color:var(--muted)}
.article-meta{display:flex;gap:8px;align-items:center;margin-top:5px;font-size:8.5px;color:var(--muted)}
.pill{border:1px solid #cfd6e0;background:#f1f4f8;border-radius:3px;padding:1px 6px;font-size:8px;color:#4a5d80}

/* calendar */
.calendar{left:560px;top:732px;width:250px;border:1px solid var(--line)}
.cal-head{height:30px;background:var(--cal-head);color:var(--white);display:flex;justify-content:space-between;align-items:center;padding:0 10px;font-size:12px}
.cal-grid{display:grid;grid-template-columns:repeat(7,1fr)}
.cal-grid span{height:31px;display:flex;align-items:center;justify-content:center;font-size:10.5px;border-right:1px solid var(--line);border-bottom:1px solid var(--line)}
.cal-grid .dow{height:22px;font-size:8.5px;color:var(--muted);background:#f6f6f6}
.cal-grid .out{color:#bbb}
.cal-grid .today{background:#3f7fd9;color:var(--white)}

/* social */
.social{left:560px;top:1025px;display:flex;gap:12px}
.social span{width:32px;height:32px;border-radius:50%}

/* footer */
.site-footer{left:0;top:1120px;width:861px;height:80px;background:var(--footer);color:#bdbdbd;font-size:10px;padding:16px 57px}
.site-footer p{margin-bottom:10px}
.footer-social{right:57px;top:1134px;display:flex;gap:6px}
.footer-social span{width:20px;height:20px}
</style>
</head>
<body>

<header>
  <div class="abs brand"><span class="brand-dot"></span><span class="brand-name">Ironhaus</span></div>
  <div class="abs search"><span>Search...</span>
    <svg width="11" height="11" viewBox="0 0 12 12"><circle cx="5" cy="5" r="3.8" fill="none" stroke="#888" stroke-width="1.5"/><line x1="8" y1="8" x2="11" y2="11" stroke="#888" stroke-width="1.5"/></svg>
  </div>
</header>

<nav class="abs main-nav">
  <a class="is-active" href="#">Home</a><a href="#">About us</a><a href="#">Team</a><a href="#">Gallery</a><a href="#">Membership</a><a href="#">Classes</a><a href="#">Member Log In</a><a href="#">Contact Us</a><a href="#">Location</a>
</nav>

<section class="abs hero" role="img" aria-label="Photo of gym members training on cardio machines"></section>
<div class="abs hero-caption">
  <h1>Gym Fitness amd Training</h1>
  <p>Train hard with expert coaches, open floors and no hidden fees in the biggest club around.</p>
</div>
<div class="abs hero-arrow" style="left:40px"><svg width="30" height="30" viewBox="0 0 30 30"><path d="M17 9l-6 6 6 6" fill="none" stroke="#fff" stroke-width="2"/></svg></div>
<div class="abs hero-arrow" style="left:791px"><svg width="30" height="30" viewBox="0 0 30 30"><path d="M13 9l6 6-6 6" fill="none" stroke="#fff" stroke-width="2"/></svg></div>

<article class="abs feature" style="left:57px;width:244px">
  <h2>What's Next</h2>
  <p class="sub">Upcoming Classes</p>
  <ul class="class-list rule">
    <li><svg width="10" height="10" viewBox="0 0 10 10"><circle cx="5" cy="5" r="4" fill="none" stroke="#fff"/><path d="M5 2.5V5h2" fill="none" stroke="#fff"/></svg><span class="name">Gym Fitness</span><span>12:30 - 13:30</span></li>
    <li><svg width="10" height="10" viewBox="0 0 10 10"><circle cx="5" cy="5" r="4" fill="none" stroke="#fff"/><path d="M5 2.5V5h2" fill="none" stroke="#fff"/></svg><span class="name">Boxing</span><span>12:30 - 13:30</span></li>
    <li><svg width="10" height="10" viewBox="0 0 10 10"><circle cx="5" cy="5" r="4" fill="none" stroke="#fff"/><path d="M5 2.5V5h2" fill="none" stroke="#fff"/></svg><span class="name">Yoga pilates</span><span>12:30 - 13:30</span></li>
  </ul>
</article>

<article class="abs feature" style="left:308px;width:247px">
  <h2>Membership Cards</h2>
  <p class="sub">25% discount for all members</p>
  <div class="offer rule">
    <span class="offer-icon"><svg width="18" height="14" viewBox="0 0 18 14"><rect x="1" y="1" width="16" height="12" rx="2" fill="none" stroke="#c3161c" stroke-width="2"/><line x1="1" y1="5" x2="17" y2="5" stroke="#c3161c" stroke-width="2"/></svg></span>
    <span>Discount on services and treatments at the Ironhaus for all membership cards holders</span>
  </div>
  <span class="more">More.</span>
</article>

<article class="abs feature" style="left:563px;width:247px">
  <h2>Classes</h2>
  <p class="sub">Signup Today</p>
  <div class="offer rule">
    <span class="offer-icon"><svg width="16" height="16" viewBox="0 0 16 16"><circle cx="8" cy="8" r="6.5" fill="none" stroke="#c3161c" stroke-width="2"/><path d="M8 4v4h3" fill="none" stroke="#c3161c" stroke-width="2"/></svg></span>
    <span>Discount on services and treatments at the Ironhaus for all membership cards holders</span>
  </div>
  <span class="more">More.</span>
</article>

<h2 class="abs section-title" style="left:57px;top:732px">Latest Articles</h2>

<article class="abs article" style="top:765px">
  <div class="article-thumb" role="img" aria-label="Photo of a member lifting weights"></div>
  <div>
    <h3>Suspendisse eu erat quam. Vivamus porttitor eros quis.</h3>
    <p>Our new strength floor opens this month with fresh racks, more benches and longer hours so every member can train on their own schedule without waiting.</p>
    <div class="article-meta"><span>Posted on 02 June 2012</span><span class="pill">chirplo</span><span class="pill">kinwall</span></div>
  </div>
</article>

<article class="abs article" style="top:865px">
  <div class="article-thumb" role="img" aria-label="Photo of a group fitness class"></div>
  <div>
    <h3>Suspendisse eu erat quam. Vivamus porttitor eros quis.</h3>
    <p>Bring your own trainer at no extra cost. Freelance coaches can book our activity rooms and grow their classes with members from across the whole city.</p>
    <div class="article-meta"><span>Posted on 02 June 2012</span><span class="pill">chirplo</span><span class="pill">kinwall</span></div>
  </div>
</article>

<article class="abs article" style="top:965px">
  <div class="article-thumb" role="img" aria-label="Photo of a trainer coaching a member"></div>
  <div>
    <h3>Suspendisse eu erat quam. Vivamus porttitor eros quis.</h3>
    <p>Daily, monthly, six month and annual plans are now live. No joining fee, no hidden charges, just honest pricing and service that matches the best hotel gyms.</p>
    <div class="article-meta"><span>Posted on 02 June 2012</span><span class="pill">chirplo</span><span class="pill">kinwall</span></div>
  </div>
</article>

<aside class="abs calendar">
  <div class="cal-head">
    <svg width="8" height="10" viewBox="0 0 8 10"><path d="M6 1L2 5l4 4" fill="none" stroke="#fff" stroke-width="1.6"/></svg>
    <span>January 2012</span>
    <svg width="8" height="10" viewBox="0 0 8 10"><path d="M2 1l4 4-4 4" fill="none" stroke="#fff" stroke-width="1.6"/></svg>
  </div>
  <div class="cal-grid">
    <span class="dow">MON</span><span class="dow">TUE</span><span class="dow">WED</span><span class="dow">THU</span><span class="dow">FRI</span><span class="dow">SAT</span><span class="dow">SUN</span>
    <span class="out">31</span><span>1</span><span>2</span><span>3</span><span>4</span><span>5</span><span>6</span>
    <span>7</span><span>8</span><span>9</span><span>10</span><span>11</span><span>12</span><span class="today">13</span>
    <span>14</span><span>15</span><span>16</span><span>17</span><span>18</span><span>19</span><span>20</span>
    <span>21</span><span>22</span><span>23</span><span>24</span><span>25</span><span>26</span><span>27</span>
    <span>28</span><span>29</span><span>30</span><span>31</span><span class="out">1</span><span class="out">2</span><span class="out">3</span>
  </div>
</aside>

<h2 class="abs section-title" style="left:560px;top:990px">Follow us on</h2>
<div class="abs social">
  <span style="background:var(--blue)" aria-label="kinwall"></span>
  <span style="background:var(--sky)" aria-label="chirplo"></span>
  <span style="background:var(--teal)" aria-label="snapvault"></span>
  <span style="background:var(--rose)" aria-label="brawnmesh"></span>
</div>

<footer class="abs site-footer">
  <p>Terms and Conditions | Privacy Policy | Site Map</p>
  <p>Copyright © 2013, All Rights Reserved</p>
</footer>
<div class="abs footer-social">
  <span style="background:var(--blue)"></span><span style="background:var(--sky)"></span><span style="background:#e07b22"></span><span style="background:var(--rose)"></span>
</div>

</body>
</html>
```